Business Card and Letterhead for Pimlu - modern real estate business

I need a double sided business card design for Pimlu. Please see business card brief here https://files.trelvonadocs.com/sheet/r/7QzTmWbaXLJnoPEd-kRyUgFhHsstbvCe2qfoMxDa_pz/view?mode=shared

Please feel free to design the business cards however you feel best. I am happy to give some creative freedoms and then provide feedback from there.

Please then also create a letterhead to match the business card design

Colors

Designer to choose colors to be used in the design.

Requirements
Must have
• Must be a modern, elegant business card which looks very professional

```html
<!DOCTYPE html>
<html lang="en">
<head>
<meta charset="utf-8">
<title>Pimlu Business Card</title>
<link rel="stylesheet" href="https://fonts.googleapis.com/css2?family=Roboto:wght@400;500;700;900&display=swap">
<style>
  :root {
    --brand-red: #e41e26;
    --ink: #2b2b2b;
    --card-white: #ffffff;
    --card-black: #171717;
    --backdrop: #d9d9d6;
    --photo-sky: #c9d3d6;
    --photo-green: #7e9466;
    --photo-suit: #2d3036;
  }
  * { box-sizing: border-box; margin: 0; padding: 0; }
  html, body { width: 1200px; height: 919px; overflow: hidden; }
  body {
    background: var(--backdrop);
    font-family: "Roboto", Arial, sans-serif;
    display: flex;
    flex-direction: column;
    align-items: center;
    justify-content: center;
    gap: 32px;
  }
  .card {
    width: 720px;
    height: 411px;
    position: relative;
    overflow: hidden;
    box-shadow: 0 6px 18px rgba(0,0,0,0.18);
  }

  /* Front */
  .card-front { background: var(--card-white); }
  .portrait-area {
    position: absolute;
    top: 0; right: 0;
    width: 430px; height: 100%;
    background:
      linear-gradient(90deg, var(--card-white) 0%, rgba(255,255,255,0) 38%),
      linear-gradient(180deg, rgba(255,255,255,0) 70%, var(--card-white) 100%),
      radial-gradient(ellipse at 70% 75%, var(--photo-suit) 0 32%, transparent 33%),
      linear-gradient(160deg, var(--photo-sky) 0%, #b8c5bc 30%, var(--photo-green) 65%, #a7b27a 100%);
  }
  .front-content {
    position: absolute;
    left: 52px; top: 46px;
    width: 320px;
  }
  .brand-name {
    font-weight: 700;
    font-size: 56px;
    letter-spacing: 2px;
    color: var(--brand-red);
    text-transform: uppercase;
    line-height: 1;
  }
  .agent-name {
    margin-top: 34px;
    font-weight: 700;
    font-size: 22px;
    letter-spacing: 1.5px;
    color: var(--brand-red);
    text-transform: uppercase;
  }
  .agent-title {
    font-size: 17px;
    color: var(--ink);
    margin-top: 2px;
  }
  .postal-address {
    margin-top: 20px;
    font-size: 17px;
    line-height: 1.3;
    color: var(--ink);
    font-style: normal;
  }
  .contact-list {
    list-style: none;
    margin-top: 18px;
    font-size: 17px;
    line-height: 1.45;
    color: var(--ink);
  }
  .contact-list li { display: flex; align-items: center; gap: 10px; }
  .contact-icon { width: 16px; height: 16px; flex: none; }
  .accent { color: var(--brand-red); }

  /* Back */
  .card-back {
    background: var(--card-black);
    display: flex;
    flex-direction: column;
    align-items: center;
    justify-content: center;
  }
  .back-brand {
    font-weight: 700;
    font-size: 128px;
    letter-spacing: 6px;
    color: var(--brand-red);
    text-transform: uppercase;
    line-height: 1;
  }
  .back-web {
    margin-top: 56px;
    font-size: 20px;
    letter-spacing: 1.5px;
    color: #ffffff;
  }
</style>
</head>
<body>

<section class="card card-front">
  <div class="portrait-area" role="img" aria-label="Portrait photo of the agent in a dark suit against a leafy valley view"></div>
  <div class="front-content">
    <div class="brand-name">Pimlu</div>
    <p class="agent-name">Reid Hollis</p>
    <p class="agent-title">Licenced Real Estate Agent</p>
    <address class="postal-address">PO Box 3150<br>Larrowby NSW 2690</address>
    <ul class="contact-list">
      <li>
        <svg class="contact-icon" viewBox="0 0 16 16" aria-hidden="true"><circle cx="8" cy="8" r="8" fill="var(--brand-red)"/><path d="M5 4.5c.5-.4 1-.3 1.3.2l.6 1c.2.4.1.8-.2 1l-.4.3c.4.9 1 1.5 1.9 1.9l.3-.4c.2-.3.6-.4 1-.2l1 .6c.5.3.6.8.2 1.3-.6.8-1.5 1-2.5.5C6.6 10 5.9 9.3 5.3 8 4.8 6.8 4.4 5.2 5 4.5z" fill="#fff"/></svg>
        0412 309 584
      </li>
      <li>
        <svg class="contact-icon" viewBox="0 0 16 16" aria-hidden="true"><rect x="1" y="3" width="14" height="10" rx="1" fill="var(--brand-red)"/><path d="M1.5 3.8 8 9l6.5-5.2" stroke="#fff" stroke-width="1.2" fill="none"/></svg>
        reid@pimlu.com
      </li>
      <li>
        <svg class="contact-icon" viewBox="0 0 16 16" aria-hidden="true"><circle cx="8" cy="8" r="8" fill="var(--brand-red)"/><path d="M2 8h12M8 1.5c-2.4 3.5-2.4 9.5 0 13M8 1.5c2.4 3.5 2.4 9.5 0 13" stroke="#fff" stroke-width="1" fill="none"/></svg>
        www.<span class="accent">pimlu</span>.com
      </li>
    </ul>
  </div>
</section>

<section class="card card-back">
  <div class="back-brand">Pimlu</div>
  <p class="back-web">www.<span class="accent">pimlu</span>.com</p>
</section>

</body>
</html>
```